Swing Dance Themed Cleaning Company Website

We need a website designed for a cleaning company based in Portland, Oregon called Foxtrot Lane. We clean homes and commercial buildings, inside and out.

needs to be vintage and like the velvet tambour. Speakeasy 1920s feel.
needs to be classy.

Check out foxtrotlane.com We are not happy with the site currently.

please look at house scout site for more content https://www.housescoutpro.com/rated.FoxtrotLaneCleaning.48217705.html

Check out my videos on my ClipHaven channel Foxtrot Lane

Target Market(s)

middle class and home owner

Industry/Entity Type

Cleaning Service

Number of Pages Required

3 page

Font styles to use
Other font styles liked:
• jazzrag

Colors

Designer to choose colors to be used in the design.

Requirements
Must have
• must be good on pc and mobile

```html
<!DOCTYPE html>
<html lang="en">
<head>
<meta charset="utf-8">
<title>Foxtrot Lane — Cleaning Services in Portland</title>
<link href="https://fonts.googleapis.com/css2?family=Jost:wght@400;500;700&family=Montserrat:wght@700&family=Open+Sans:wght@400;700&display=swap" rel="stylesheet">
<style>
:root{
  --cream:#f5f1e7;
  --ink:#1f1f1f;
  --panel:#2b2a28;
  --black:#000;
  --yellow:#f5e414;
  --white:#fff;
}
*{box-sizing:border-box;margin:0;padding:0}
html,body{width:1200px;height:2965px;overflow:hidden}
body{position:relative;background:var(--cream);color:var(--ink);font-family:"Open Sans",sans-serif}
.abs{position:absolute}
.center{text-align:center}

/* header */
.site-header{left:132px;top:6px;width:936px;height:116px;background:var(--black)}
.brand{left:16px;top:32px;display:flex;align-items:center;gap:12px}
.brand-square{width:26px;height:26px;background:var(--yellow)}
.brand-name{font-family:"Jost",sans-serif;font-weight:500;font-size:30px;line-height:1;color:var(--yellow);white-space:nowrap}
.brand-tag{left:16px;top:90px;font-family:"Jost",sans-serif;font-size:13px;color:var(--yellow);letter-spacing:.3px}
.header-phone{right:20px;top:26px;font-family:"Montserrat",sans-serif;font-weight:700;font-size:23px;color:var(--white);display:flex;align-items:center;gap:10px}
.main-nav{right:22px;top:80px;display:flex;gap:34px;font-family:"Jost",sans-serif;font-size:16px;color:var(--white)}
.main-nav .active{color:var(--yellow)}

/* video */
.hero-video{left:132px;top:130px;width:936px;height:443px;background:linear-gradient(180deg,#2e2623 0%,#3a2c25 55%,#5a3a26 100%)}
.play-btn{left:445px;top:198px}

/* about */
.about-art{left:134px;top:636px;width:356px;height:296px;background:linear-gradient(180deg,#e7e1d3,#d9d1bf)}
.about h2{left:514px;top:628px;font-family:"Jost",sans-serif;font-weight:400;font-size:56px}
.about .lead{left:514px;top:696px;width:560px;font-family:"Jost",sans-serif;font-size:33px;line-height:1.25}
.about h3{left:514px;top:798px;font-family:"Open Sans",sans-serif;font-weight:700;font-size:21px;letter-spacing:.5px}
.about p{left:514px;top:834px;width:530px;font-size:13.5px;line-height:1.55}
.btn{display:inline-block;border:1.5px solid #555;background:transparent;font-family:"Jost",sans-serif;font-size:15px;color:var(--ink);padding:8px 16px}
.about .actions{left:514px;top:892px;display:flex;gap:16px}

/* pricing */
.pricing{left:132px;top:1002px;width:936px;height:236px}
.pricing h2{left:0;top:46px;width:936px;font-family:"Jost",sans-serif;font-weight:400;font-size:44px;color:var(--white)}
.pricing p{left:0;top:104px;width:936px;font-family:"Jost",sans-serif;font-size:25px;line-height:1.35;color:var(--white)}

/* services */
.services h2{left:0;top:1288px;width:1200px;font-family:"Jost",sans-serif;font-weight:400;font-size:64px}
.services .intro{left:140px;top:1362px;width:920px;font-size:13.5px;line-height:1.55}
.service{width:320px;top:1424px}
.service h3{margin-top:16px;font-family:"Jost",sans-serif;font-weight:400;font-size:17px;text-transform:uppercase}
.service ul{list-style:none;margin-top:8px;font-size:12.5px;line-height:21px}

/* blog */
.blog{left:132px;top:1817px;width:936px;height:668px}
.blog h2{left:0;top:56px;width:936px;font-family:"Jost",sans-serif;font-weight:400;font-size:44px;color:var(--white)}
.post{top:134px;width:421px;height:394px;background:var(--white)}
.post-img{width:421px;height:230px}
.post h3{margin:16px 20px 0;font-family:"Jost",sans-serif;font-weight:400;font-size:20px;line-height:1.3}
.post .meta{margin:14px 20px 0;font-size:10px}
.post .excerpt{margin:14px 20px 0;font-size:10.5px;line-height:1.6}
.post .excerpt u{text-decoration:underline}
.blog .btn{color:var(--white);border-color:var(--white)}

/* contact */
.contact h2{left:0;top:2536px;width:1200px;font-family:"Jost",sans-serif;font-weight:400;font-size:60px}
.contact .intro{left:0;top:2610px;width:1200px;font-size:13.5px}
.contact .address{left:0;top:2638px;width:1200px;font-family:"Jost",sans-serif;font-size:22px}
.contact .direct{left:0;top:2672px;width:1200px;font-family:"Montserrat",sans-serif;font-weight:700;font-size:23px;letter-spacing:.5px}

/* footer */
.site-footer{left:132px;top:2817px;width:936px;height:148px}
.social{left:0;top:40px;width:936px;display:flex;justify-content:center;gap:18px}
.social span{width:14px;height:14px;border-radius:50%;background:var(--white)}
.footer-nav{left:0;top:74px;width:936px;font-size:11px;color:var(--white)}
.copyright{left:0;top:96px;width:936px;font-size:11px;color:var(--white)}
</style>
</head>
<body>

<header class="site-header abs">
  <div class="brand abs"><span class="brand-square"></span><span class="brand-name">Foxtrot Lane</span></div>
  <div class="brand-tag abs">SPOTLESS HOMES ACROSS PORTLAND</div>
  <div class="header-phone abs">
    <svg width="18" height="18" viewBox="0 0 24 24" aria-hidden="true"><path fill="#fff" d="M6.6 10.8a15.1 15.1 0 0 0 6.6 6.6l2.2-2.2c.3-.3.7-.4 1-.2 1.1.4 2.3.6 3.6.6.6 0 1 .4 1 1V20c0 .6-.4 1-1 1A17 17 0 0 1 3 4c0-.6.4-1 1-1h3.5c.6 0 1 .4 1 1 0 1.3.2 2.5.6 3.6.1.3 0 .7-.2 1z"/></svg>
    503-555-0148
  </div>
  <nav class="main-nav abs"><span class="active">Home</span><span>About Us</span><span>Services</span><span>Blog</span><span>Contact Us</span></nav>
</header>

<section class="hero-video abs" role="img" aria-label="Promotional video still: a cleaner mopping a wooden dance floor with the word Cleaners lettered across it">
  <svg class="play-btn abs" width="46" height="46" viewBox="0 0 46 46" aria-hidden="true"><circle cx="23" cy="23" r="23" fill="#fff"/><path d="M18 13l15 10-15 10z" fill="#222"/></svg>
</section>

<section class="about">
  <div class="about-art abs" role="img" aria-label="Vintage ink illustration of a dapper man dancing with a mop"></div>
  <h2 class="abs">About Us</h2>
  <p class="lead abs">Making the greater Portland area clean, one building at a time</p>
  <h3 class="abs">GOOD PEOPLE, GREAT SERVICE</h3>
  <p class="abs">Foxtrot Lane is a family owned professional cleaning business. We provide our years of cleaning experience to homes and businesses in and around Portland, Oregon.</p>
  <div class="actions abs"><span class="btn">Read More</span><span class="btn">Leave a Review</span></div>
</section>

<section class="pricing abs center">
  <svg class="abs" style="left:0;top:0" width="936" height="236" viewBox="0 0 936 236" aria-hidden="true"><path d="M0 0H936V232Q468 188 0 232Z" fill="var(--panel)"/></svg>
  <h2 class="abs">Pricing</h2>
  <p class="abs">$80 per 1,000 square feet for usual housekeeping services,<br>call for an estimate for other services</p>
</section>

<section class="services">
  <h2 class="abs center">Our Services</h2>
  <p class="intro abs center">We provide cleaning and janitorial services for one-time and recurring needs. While this isn't an exhaustive list of available services, these are certainly the most commonly requested!</p>

  <div class="service abs center" style="left:115px">
    <svg width="176" height="176" viewBox="0 0 176 176" aria-hidden="true"><circle cx="88" cy="88" r="84" fill="var(--panel)"/><circle cx="88" cy="88" r="76" fill="none" stroke="var(--cream)" stroke-width="3"/><g fill="none" stroke="#fff" stroke-width="2.5"><path d="M92 52L88 104"/><path d="M80 104h16l6 20H72z"/></g></svg>
    <h3>General House Keeping</h3>
    <ul><li>• Floor to ceiling dusting</li><li>• Cobweb removal</li><li>• Kitchen Cleaning</li><li>• Bathroom cleaning</li><li>• Sweep, mop and vacuum floors</li></ul>
  </div>

  <div class="service abs center" style="left:439px">
    <svg width="176" height="176" viewBox="0 0 176 176" aria-hidden="true"><circle cx="88" cy="88" r="84" fill="var(--panel)"/><circle cx="88" cy="88" r="76" fill="none" stroke="var(--cream)" stroke-width="3"/><g fill="none" stroke="#fff" stroke-width="2.5" stroke-linejoin="round"><path d="M58 70l30-14 30 14-30 14z"/><path d="M58 70v36l30 14 30-14V70"/><path d="M88 84v36"/></g></svg>
    <h3>Move Outs &amp; Detail</h3>
    <ul><li>• All general house keeping</li><li>• Make your house "move in" ready</li><li>• Refrigerator and oven cleaning</li><li>• Window washing</li><li>• Carpet cleaning</li></ul>
  </div>

  <div class="service abs center" style="left:763px">
    <svg width="176" height="176" viewBox="0 0 176 176" aria-hidden="true"><circle cx="88" cy="88" r="84" fill="var(--panel)"/><circle cx="88" cy="88" r="76" fill="none" stroke="var(--cream)" stroke-width="3"/><g fill="none" stroke="#fff" stroke-width="3"><path d="M50 56h76v10H50z"/><path d="M56 66q26 8 24 22v38h16V88q-2-14 24-22"/></g></svg>
    <h3>Exterior Services</h3>
    <ul><li>• Leaf blowing</li><li>• Pressure washing</li><li>• Window washing</li><li style="line-height:14px;margin:3px 0">• Exterior house detail<br>(removes moss, dirt, cobwebs etcetera)</li><li>• Gutter cleaning</li></ul>
  </div>
</section>

<section class="blog abs center">
  <svg class="abs" style="left:0;top:0" width="936" height="668" viewBox="0 0 936 668" aria-hidden="true"><path d="M0 0H936V640Q468 690 0 640Z" fill="var(--panel)"/></svg>
  <h2 class="abs">Blog</h2>
  <article class="post abs" style="left:24px;text-align:left">
    <div class="post-img" role="img" aria-label="Photo of a bass player performing at an outdoor music festival" style="background:linear-gradient(160deg,#4a5a36,#6b4a32 60%,#8a3a2a)"></div>
    <h3>Foxtrot Lane Returns to Riverside Rhythm Festival 2017</h3>
    <p class="meta">Posted in Events by Martin Hale on July 15, 2017</p>
    <p class="excerpt">Foxtrot Lane returns to the Riverside Rhythm Festival this June 30 through July 4, 2017.&nbsp; Say hi to us as we run a kids. <u>More</u></p>
  </article>
  <article class="post abs" style="left:491px;text-align:left">
    <div class="post-img" role="img" aria-label="Photo of a smiling festival-goer in a colorful flowered hat" style="background:linear-gradient(160deg,#7a9a5a,#d66a8a 55%,#5a6a9a)"></div>
    <h3>Foxtrot Lane sponsoring Riverside Rhythm Fest 2016</h3>
    <p class="meta">Posted in Events by Martin Hale on July 15, 2017</p>
    <p class="excerpt">Foxtrot Lane will be sponsoring the Kids Booth at the Riverside Rhythm Festival in July! http://www.riversiderhythmfest.com/ <u>More</u></p>
  </article>
  <span class="btn abs" style="left:415px;top:563px">Read More</span>
</section>

<section class="contact center">
  <h2 class="abs">Contact Us</h2>
  <p class="intro abs">Contact us for a quote, to book a cleaning, or for any other reason. We're looking forward to hearing from you!</p>
  <p class="address abs">418 SE Alder St #207, Portland, OR 97214</p>
  <p class="direct abs">503-555-0148 &nbsp;&nbsp;|&nbsp;&nbsp; martin@foxtrotlane.com</p>
  <span class="btn abs" style="left:543px;top:2718px">Contact Form</span>
</section>

<footer class="site-footer abs center">
  <svg class="abs" style="left:0;top:0" width="936" height="148" viewBox="0 0 936 148" aria-hidden="true"><path d="M0 30Q468 -12 936 30V148H0Z" fill="var(--panel)"/></svg>
  <div class="social abs" aria-label="Social links"><span></span><span></span><span></span><span></span><span></span></div>
  <p class="footer-nav abs">Home &nbsp;|&nbsp; About Us &nbsp;|&nbsp; Services &nbsp;|&nbsp; Blog &nbsp;|&nbsp; Contact Us</p>
  <p class="copyright abs">Copyright © 2018 Foxtrot Lane.&nbsp; All rights reserved.</p>
</footer>

</body>
</html>
```